Business card design for holistic health care clinic

We need a double-sided business card design for our holistic health care clinic that integrates our logo design and also its color scheme. My business is called Valmira. It is an integrative medicine clinic. You have already done the logo for me. Please ensure an elegant and upscale design that is not cluttered, but still has all the necessary information (please see below for details).

Target Market(s)

Wellness, fitness, rehabilitation for educated, well-traveled open-minded clients who are focused on natural, organic, balanced and preventive healthcare and lifestyle.

Industry/Entity Type

Medical

Contact Information for Business Card

Modern, clean.

Number of Pages Required

1 page

Font styles to use
Serif
Sans Serif

Colors

Designer to choose colors to be used in the design.

Requirements
Must have
• Logo on one side, all other information on the other side.
• Other information should include:
• Tobias Wrenfeld - DOE, CPT, LMT
• 4100 East Marrow Drive
• Austin, TX 78119
• 512 555 0148
• 818 555 0192
• info@ValmiraHealth.example
• t.wrenfeld@ValmiraHealth.example
Nice to have
• Darker background on front - but not totally black - shaded/dark gray.

```html
<!DOCTYPE html>
<html lang="en">
<head>
<meta charset="utf-8">
<title>Valmira Business Cards</title>
<link href="https://fonts.googleapis.com/css2?family=Nunito:wght@400;700;800&display=swap" rel="stylesheet">
<style>
  :root {
    --backdrop: #262626;
    --paper: #f1f1f1;
    --paper-grey: #a4a4a4;
    --brand-blue: #0a8fcf;
    --ink: #555555;
    --white: #ffffff;
  }
  * { margin: 0; padding: 0; box-sizing: border-box; }
  html, body {
    width: 1200px; height: 961px; overflow: hidden;
    background: var(--backdrop);
    font-family: "Nunito", sans-serif;
  }
  .canvas { position: relative; width: 1200px; height: 961px; }
  .card {
    position: absolute; top: 220px; width: 297px; height: 520px;
    background: var(--paper); overflow: hidden;
  }
  .card--contact { left: 150px; }
  .card--logo-light { left: 466px; }
  .card--logo-grey { left: 782px; background: var(--paper-grey); }

  .block { position: absolute; left: 0; width: 100%; text-align: center; }

  .wordmark {
    font-weight: 800; color: var(--brand-blue);
    font-size: 46px; line-height: 1; letter-spacing: 0.5px;
  }
  .tagline {
    font-weight: 700; color: var(--brand-blue);
    font-size: 14px; line-height: 1; margin-top: 6px;
  }

  .card--contact .brand { top: 76px; }
  .card--logo-light .brand,
  .card--logo-grey .brand { top: 240px; }

  .holder { top: 300px; }
  .holder-name {
    font-weight: 700; color: var(--brand-blue);
    font-size: 26px; line-height: 1; letter-spacing: -0.5px;
  }
  .holder-credentials {
    font-weight: 700; color: var(--brand-blue);
    font-size: 14px; margin-top: 4px;
  }

  .divider {
    position: absolute; left: 139px; width: 19px; height: 1px;
    background: var(--ink); opacity: 0.7;
  }
  .divider--one { top: 340px; }
  .divider--two { top: 396px; }

  .address {
    top: 353px; color: var(--ink); font-size: 13px; line-height: 15px;
  }
  .contact-lines {
    top: 406px; color: var(--ink); font-size: 13px; line-height: 17px;
  }
  .contact-lines .label { color: var(--brand-blue); font-weight: 800; }

  .band {
    position: absolute; left: 0; bottom: 0; width: 100%; height: 39px;
    background: var(--brand-blue); color: var(--white);
    font-weight: 700; font-size: 12px;
    display: flex; align-items: center; justify-content: center;
  }
</style>
</head>
<body>
<main class="canvas">

  <section class="card card--contact" aria-label="Card back with contact details">
    <div class="block brand">
      <div class="wordmark">VALMIRA</div>
      <div class="tagline">Integrative Holistic Medicine</div>
    </div>
    <div class="block holder">
      <div class="holder-name">TOBIAS WRENFELD</div>
      <div class="holder-credentials">DOE, CPT, LMT</div>
    </div>
    <div class="divider divider--one"></div>
    <div class="block address">
      <p>4100 East Marrow Drive</p>
      <p>Austin, TX 78119</p>
    </div>
    <div class="divider divider--two"></div>
    <div class="block contact-lines">
      <p><span class="label">P.</span> 512 555 0148</p>
      <p><span class="label">M.</span> 818 555 0192</p>
      <p><span class="label">E.</span> t.wrenfeld@ValmiraHealth.example</p>
    </div>
    <div class="band">www.ValmiraHealth.example</div>
  </section>

  <section class="card card--logo-light" aria-label="Card front, light version">
    <div class="block brand">
      <div class="wordmark">VALMIRA</div>
      <div class="tagline">Integrative Holistic Medicine</div>
    </div>
    <div class="band">Helping the body help itself</div>
  </section>

  <section class="card card--logo-grey" aria-label="Card front, grey version">
    <div class="block brand">
      <div class="wordmark">VALMIRA</div>
      <div class="tagline">Integrative Holistic Medicine</div>
    </div>
    <div class="band">Helping the body help itself</div>
  </section>

</main>
</body>
</html>
```